A clean crisp business card for a Landscape Construction company. Designed to be easy to read contact/ info and also be appealing/interesting, unlike a traditional business card.

Industry/Entity Type

Landscape Construction

Contact Information for Business Card

Company name : Brambleford Landscape Construction, phone number: (877) 62Vista, website:Bramblefordyards.example, Email, sales@bramblefordyards.example

Requirements
Nice to have
• Luxurious finishes/ details…. Icons or emblems next to contact info
Should not have
• Clipart or general pictures

```html
<!DOCTYPE html>
<html lang="en">
<head>
<meta charset="utf-8">
<title>Brambleford Landscape Construction – Business Card</title>
<link rel="stylesheet" href="https://fonts.googleapis.com/css2?family=Cinzel:wght@500&family=Open+Sans:wght@400;600&display=swap">
<style>
  :root {
    --backdrop: #2e2e30;
    --lime: #9fcc3b;
    --lime-deep: #86b42c;
    --lime-emboss: #8dbd31;
    --charcoal: #232325;
    --blue: #2f78c8;
    --ink-light: #f2f2f2;
  }
  * { margin: 0; padding: 0; box-sizing: border-box; }
  html, body { width: 1200px; height: 900px; overflow: hidden; }
  body {
    background: var(--backdrop);
    display: flex;
    flex-direction: column;
    align-items: center;
    justify-content: center;
    gap: 40px;
  }
  .card {
    width: 700px;
    height: 400px;
    position: relative;
  }
  .card-front {
    background: var(--lime);
    display: flex;
    align-items: center;
    justify-content: center;
  }
  .wordmark {
    font-family: "Cinzel", serif;
    font-weight: 500;
    text-align: center;
    line-height: 1.1;
  }
  .wordmark .wordmark-name { font-size: 52px; display: block; }
  .wordmark .wordmark-sub { font-size: 17px; letter-spacing: 5px; display: block; }
  .card-front .wordmark { color: var(--lime-emboss); }

  .card-back {
    background: var(--charcoal);
    display: flex;
    align-items: center;
    padding: 0 40px 0 36px;
  }
  .card-back .wordmark {
    color: var(--lime);
    width: 300px;
  }
  .card-back .wordmark .wordmark-name { font-size: 40px; }
  .card-back .wordmark .wordmark-sub { font-size: 13px; letter-spacing: 3.5px; }

  .divider {
    width: 4px;
    height: 210px;
    margin: 0 26px 0 24px;
    display: flex;
    flex-direction: column;
    align-items: center;
  }
  .divider .seg-lime { width: 2px; flex: 0 0 30px; background: var(--lime); }
  .divider .seg-blue { width: 4px; flex: 1; background: var(--blue); }
  .divider .seg-lime-end { width: 2px; flex: 0 0 40px; background: var(--lime); }

  .contact {
    font-family: "Open Sans", sans-serif;
    color: var(--ink-light);
  }
  .person-name {
    font-family: "Cinzel", serif;
    font-weight: 500;
    font-size: 28px;
    letter-spacing: 2px;
    line-height: 1;
  }
  .person-name .first { color: var(--blue); }
  .person-name .last { color: var(--lime); }
  .person-role { font-size: 15px; margin: 4px 0 14px; }
  .address { font-size: 14.5px; line-height: 1.55; margin-bottom: 12px; }
  .contact-list { list-style: none; font-size: 15px; }
  .contact-list li { display: flex; align-items: center; gap: 10px; line-height: 1.85; }
  .contact-list svg { width: 16px; height: 16px; flex: none; fill: var(--lime); }
</style>
</head>
<body>

  <section class="card card-front" aria-label="Card front">
    <div class="wordmark">
      <span class="wordmark-name">Brambleford</span>
      <span class="wordmark-sub">Landscape Construction</span>
    </div>
  </section>

  <section class="card card-back" aria-label="Card back">
    <div class="wordmark">
      <span class="wordmark-name">Brambleford</span>
      <span class="wordmark-sub">Landscape Construction</span>
    </div>

    <div class="divider" aria-hidden="true">
      <span class="seg-lime"></span>
      <span class="seg-blue"></span>
      <span class="seg-lime-end"></span>
    </div>

    <div class="contact">
      <p class="person-name"><span class="first">Marcus</span> <span class="last">Hale</span></p>
      <p class="person-role">Director</p>
      <p class="address">4710 Alder Hollow Rd.,<br>Suite 118, Fernwick, OH 45990</p>
      <ul class="contact-list">
        <li>
          <svg viewBox="0 0 24 24" aria-hidden="true"><path d="M6.6 10.8a15.1 15.1 0 0 0 6.6 6.6l2.2-2.2a1 1 0 0 1 1-.25 11.4 11.4 0 0 0 3.6.57 1 1 0 0 1 1 1V20a1 1 0 0 1-1 1A17 17 0 0 1 3 4a1 1 0 0 1 1-1h3.5a1 1 0 0 1 1 1c0 1.25.2 2.45.57 3.57a1 1 0 0 1-.25 1z"/></svg>
          (877) 62Vista
        </li>
        <li>
          <svg viewBox="0 0 24 24" aria-hidden="true"><path d="M2 5h20v14H2z M2 5l10 8 10-8" fill="none"/><path d="M2 5h20v2l-10 7L2 7z"/><path d="M2 9l10 7 10-7v10H2z"/></svg>
          sales@bramblefordyards.example
        </li>
        <li>
          <svg viewBox="0 0 24 24" aria-hidden="true"><path d="M12 2a10 10 0 1 0 0 20 10 10 0 0 0 0-20zm6.9 6h-3a15.7 15.7 0 0 0-1.4-3.6A8 8 0 0 1 18.9 8zM12 4.1A14 14 0 0 1 13.9 8h-3.8A14 14 0 0 1 12 4.1zM4.3 14a8 8 0 0 1 0-4h3.4a16.5 16.5 0 0 0 0 4zm.8 2h3a15.7 15.7 0 0 0 1.4 3.6A8 8 0 0 1 5.1 16zm3-8h-3a8 8 0 0 1 4.4-3.6A15.7 15.7 0 0 0 8.1 8zM12 19.9A14 14 0 0 1 10.1 16h3.8a14 14 0 0 1-1.9 3.9zm2.3-5.9H9.7a14.7 14.7 0 0 1 0-4h4.6a14.7 14.7 0 0 1 0 4zm.2 5.6a15.7 15.7 0 0 0 1.4-3.6h3a8 8 0 0 1-4.4 3.6zm1.8-5.6a16.5 16.5 0 0 0 0-4h3.4a8 8 0 0 1 0 4z"/></svg>
          www.bramblefordyards.example
        </li>
      </ul>
    </div>
  </section>

</body>
</html>
```